Home Baker of cakes, muffins, cookies and pastries.

I am looking for business cards for my home baking business called " Yum Bea-A Treat " - I want them to be super cute and girly, yet simple and modern at the same time. Pastel colours is what I envision with the main colour being baby pink.

```html
<!DOCTYPE html>
<html lang="en">
<head>
<meta charset="UTF-8">
<title>Yum Bea-A Treat — Business Cards</title>
<link href="https://fonts.googleapis.com/css2?family=Lato:wght@400;700&family=Great+Vibes&display=swap" rel="stylesheet">
<style>
  :root {
    --bg: #2a2a2c;
    --card-black: #151515;
    --baby-pink: #ef8fac;
    --butter: #f7f095;
    --white: #ffffff;
    --logo-pink: #f6b3c8;
  }
  html, body {
    margin: 0;
    width: 1200px;
    height: 900px;
    overflow: hidden;
    background: var(--bg);
  }
  .sheet {
    position: relative;
    width: 1200px;
    height: 900px;
  }
  .card {
    position: absolute;
    left: 250px;
    width: 700px;
    height: 400px;
    border-radius: 22px;
    overflow: hidden;
    box-shadow: 0 14px 30px rgba(0,0,0,0.45);
  }
  .card--front { top: 35px; }
  .card--back { top: 465px; }
  .card svg { display: block; }
  .brand-name {
    font-family: "Lato", sans-serif;
    font-weight: 700;
    font-size: 40px;
    fill: var(--logo-pink);
    letter-spacing: 1px;
  }
  .brand-dot { fill: var(--butter); }
  .website {
    font-family: "Lato", sans-serif;
    font-size: 19px;
    letter-spacing: 4px;
    fill: var(--white);
  }
  .person-name {
    font-family: "Great Vibes", cursive;
    font-size: 38px;
    fill: var(--white);
  }
  .person-role {
    font-family: "Lato", sans-serif;
    font-size: 16px;
    fill: var(--white);
  }
  .contact-line {
    font-family: "Lato", sans-serif;
    font-size: 15px;
    fill: var(--white);
  }
  .contact-icon { fill: var(--white); }
  .contact-icon-mark { fill: var(--baby-pink); }
</style>
</head>
<body>
<main class="sheet">

  <section class="card card--front" aria-label="Business card front">
    <svg width="700" height="400" viewBox="0 0 700 400">
      <rect class="card-base" width="700" height="400" fill="var(--card-black)"/>
      <path class="pink-band" d="M0,400 V300 C180,220 420,170 700,160 V400 Z" fill="var(--baby-pink)"/>
      <path class="butter-swoosh" d="M10,296 C190,200 430,146 690,124 C430,158 200,216 10,296 Z" fill="var(--butter)"/>
      <g class="brand">
        <circle class="brand-dot" cx="190" cy="106" r="8"/>
        <text class="brand-name" x="208" y="120">Yum Bea-A Treat</text>
      </g>
      <text class="website" x="300" y="340" transform="rotate(-12 300 340)">www.yumbeaatreat.com</text>
    </svg>
  </section>

  <section class="card card--back" aria-label="Business card back">
    <svg width="700" height="400" viewBox="0 0 700 400">
      <rect class="card-base" width="700" height="400" fill="var(--card-black)"/>
      <path class="pink-band" d="M0,400 V300 C180,220 420,170 700,160 V400 Z" fill="var(--baby-pink)"/>
      <path class="butter-swoosh" d="M10,296 C190,200 430,146 690,124 C430,158 200,216 10,296 Z" fill="var(--butter)"/>
      <g class="brand">
        <circle class="brand-dot" cx="190" cy="86" r="8"/>
        <text class="brand-name" x="208" y="100">Yum Bea-A Treat</text>
      </g>

      <g class="owner">
        <text class="person-name" x="190" y="335" text-anchor="middle">Bea Hollander</text>
        <text class="person-role" x="190" y="362" text-anchor="middle">Owner / Founder</text>
      </g>

      <line class="divider" x1="330" y1="235" x2="330" y2="370" stroke="var(--white)" stroke-width="2" opacity="0.8"/>

      <g class="contacts">
        <circle class="contact-icon" cx="354" cy="262" r="9"/>
        <path class="contact-icon-mark" d="M349,259 q5,-4 10,0 v2 h-3 v-1 h-4 v1 h-3 Z M349,264 h10 v3 h-10 Z"/>
        <text class="contact-line" x="370" y="267">555-014-2283</text>

        <circle class="contact-icon" cx="354" cy="294" r="9"/>
        <rect class="contact-icon-mark" x="348" y="290" width="12" height="8" rx="1"/>
        <path d="M348,290 L354,295 L360,290" fill="none" stroke="var(--white)" stroke-width="1.2"/>
        <text class="contact-line" x="370" y="299">hello@yumbea-atreat.com</text>

        <circle class="contact-icon" cx="354" cy="326" r="9"/>
        <path class="contact-icon-mark" d="M354,320 a4,4 0 0 1 4,4 c0,3 -4,8 -4,8 c0,0 -4,-5 -4,-8 a4,4 0 0 1 4,-4 Z"/>
        <text class="contact-line" x="370" y="331">742 Maple Grove Ln, Springfield, OH - 45501</text>
      </g>
    </svg>
  </section>

</main>
</body>
</html>
```